Business Card - connecting 2 souls and beggining the journey of self discovery

Logo on the front
with tag line

On the back list of services and contact details

Seminars
workshops
Coaching
podcasts

Darren Whitlow
Health & Wellbeing Life Coach
0491 372 615
darren@brightcoreliving.example
brightcoreliving.example

Industry/Entity Type

Life Coaching

Contact Information for Business Card

I like the use of colour from the logo to be used. I'm not a fan of white.

Requirements
Must have
• My tagline: The journey home starts with you
Nice to have
• Use of colour that is in the Brightcore Living logo

```html
<!DOCTYPE html>
<html lang="en">
<head>
<meta charset="utf-8">
<title>Brightcore Living — Business Card</title>
<link rel="stylesheet" href="https://fonts.googleapis.com/css2?family=Poppins:wght@400;500;600&family=Josefin+Sans:wght@400&display=swap">
<style>
  :root {
    --green: #79b829;
    --green-light: #8cc63c;
    --green-dark: #4f8c17;
    --white: #ffffff;
    --ink: #1e1e1e;
    --ink-soft: #4a4a4a;
    --stage: #000000;
    --mark: #f08a24;
  }
  * { margin: 0; padding: 0; box-sizing: border-box; }
  html, body { width: 1200px; height: 1200px; overflow: hidden; background: var(--stage); }
  body { font-family: "Poppins", sans-serif; position: relative; }

  .card {
    position: absolute; left: 100px; width: 1000px; height: 555px;
    overflow: hidden; background: var(--green);
  }
  .card--back { top: 30px; }
  .card--front { top: 615px; background: var(--white); }
  .card__shapes { position: absolute; inset: 0; width: 100%; height: 100%; }

  .brand { position: absolute; display: flex; flex-direction: column; align-items: center; }
  .brand__dot { border-radius: 50%; background: var(--mark); }
  .brand__name { font-weight: 600; white-space: nowrap; }

  .card--back .brand { left: 60px; top: 40px; width: 220px; }
  .card--back .brand__dot { width: 100px; height: 100px; }
  .card--back .brand__name { color: var(--white); font-size: 22px; margin-top: 10px; }

  .tagline-side { position: absolute; left: 50px; top: 218px; color: var(--white); font-size: 22px; font-weight: 500; white-space: nowrap; }

  .services { position: absolute; left: 52px; top: 318px; list-style: none; color: var(--white); font-size: 26px; font-weight: 500; }
  .services li { height: 47px; display: flex; align-items: center; }
  .services li::before { content: ""; width: 8px; height: 8px; border-radius: 50%; background: var(--white); margin-right: 12px; }

  .person { position: absolute; left: 528px; top: 204px; }
  .person__name { font-size: 37px; font-weight: 600; color: var(--ink); line-height: 1.1; }
  .person__name span { color: var(--green); }
  .person__role { font-family: "Josefin Sans", sans-serif; font-size: 22px; color: var(--ink-soft); margin-top: 2px; }

  .contacts { position: absolute; left: 522px; top: 308px; list-style: none; }
  .contacts li { display: flex; align-items: center; height: 42px; margin-bottom: 31px; font-size: 23px; font-weight: 500; color: var(--ink); }
  .contacts svg { width: 42px; height: 42px; margin-right: 24px; flex: none; }

  .card--front .brand { left: 300px; top: 100px; width: 400px; }
  .card--front .brand__dot { width: 160px; height: 160px; }
  .card--front .brand__name { color: var(--green-dark); font-size: 32px; margin-top: 16px; }
  .tagline-main { position: absolute; left: 0; right: 0; top: 390px; text-align: center; font-size: 34px; font-weight: 500; color: var(--ink); }
</style>
</head>
<body>

<section class="card card--back" aria-label="Card back">
  <svg class="card__shapes" viewBox="0 0 720 400" preserveAspectRatio="none" aria-hidden="true">
    <defs>
      <linearGradient id="greenWash" x1="0" y1="1" x2="1" y2="0">
        <stop offset="0" stop-color="#6fae22"/>
        <stop offset="1" stop-color="#9ccf4a"/>
      </linearGradient>
    </defs>
    <rect width="720" height="400" fill="url(#greenWash)"/>
    <path d="M588,0 C400,42 232,200 160,400 L180,400 C250,205 420,45 605,0 Z" fill="#4f8c17"/>
    <path d="M605,0 C420,45 250,205 180,400 L720,400 L720,0 Z" fill="#ffffff"/>
  </svg>

  <div class="brand">
    <div class="brand__dot"></div>
    <div class="brand__name">Brightcore Living</div>
  </div>
  <p class="tagline-side">The journey home starts with you</p>

  <ul class="services">
    <li>Seminars</li>
    <li>Coaching</li>
    <li>Workshops</li>
    <li>Podcasts</li>
  </ul>

  <div class="person">
    <h1 class="person__name">Darren <span>Whitlow</span></h1>
    <p class="person__role">Health &amp; Wellbeing Life Coach</p>
  </div>

  <ul class="contacts">
    <li>
      <svg viewBox="0 0 42 42" aria-hidden="true"><circle cx="21" cy="21" r="20" fill="#79b829"/><path d="M15 12c1.5-1 2.5-.5 3 .5l1.5 3c.4 1-.2 1.7-1 2.3 1 2.3 2.6 3.9 4.7 4.8.6-.8 1.3-1.4 2.3-1l3 1.5c1 .5 1.4 1.5.5 3-1.3 2-3.3 2.6-5.5 1.6-4.8-2.1-8-5.5-9.7-10.2-.8-2.2-.3-4.2 1.2-5.5z" fill="#fff"/></svg>
      0491 372 615
    </li>
    <li>
      <svg viewBox="0 0 42 42" aria-hidden="true"><circle cx="21" cy="21" r="20" fill="#79b829"/><rect x="11" y="14" width="20" height="14" rx="1" fill="none" stroke="#fff" stroke-width="2"/><path d="M11 15l10 8 10-8" fill="none" stroke="#fff" stroke-width="2"/></svg>
      darren@brightcoreliving.example
    </li>
    <li>
      <svg viewBox="0 0 42 42" aria-hidden="true"><circle cx="21" cy="21" r="20" fill="#79b829"/><circle cx="21" cy="21" r="10" fill="none" stroke="#fff" stroke-width="2"/><path d="M11 21h20M21 11c-4 5-4 15 0 20M21 11c4 5 4 15 0 20" fill="none" stroke="#fff" stroke-width="1.6"/></svg>
      www.brightcoreliving.example
    </li>
  </ul>
</section>

<section class="card card--front" aria-label="Card front">
  <svg class="card__shapes" viewBox="0 0 720 400" preserveAspectRatio="none" aria-hidden="true">
    <path d="M345,0 L720,0 L720,200 C610,95 480,22 345,0 Z" fill="#4f8c17"/>
    <path d="M360,0 L720,0 L720,182 C615,85 490,18 360,0 Z" fill="#79b829"/>
    <path d="M0,180 C100,290 235,372 375,400 L0,400 Z" fill="#4f8c17"/>
    <path d="M0,198 C100,300 225,375 355,400 L0,400 Z" fill="#79b829"/>
  </svg>

  <div class="brand">
    <div class="brand__dot"></div>
    <div class="brand__name">Brightcore Living</div>
  </div>
  <p class="tagline-main">The journey home starts with you</p>
</section>

</body>
</html>
```